Simple Business Card Design for Tavlo

Job:

Make a very simple, minimalist business card design with my details including adjusted logo. One side to be white (with logo & text). Other side to be yellow - try plain or with logo (or part of logo eg Z). Need business card to have continuity with website.

Logo:
Our logo is made from a free download font website:
http://www.typewell.net/search.php?q=rubber
but the spacing/kerning needs correcting/adjusting as the font spaces unevenly between letters (see attached files). Need logo to be very crisp/sharp when printed.

Printing:
We will be using Plika.com so the design needs to conform to their requirements, see here:

http://uk.plika.com/products/luxe/business-cards.html (scroll down for dimensions and guidelines)

Design:

must say "plant-based food consulting" underneath logo or somewhere
no address needed in contact section
sharp corners (not rounded)
one side white, one side yellow

name: Rosalind Whitcombe
1xmobile number: +44 7700900463
1xtwiiter: @brimcounsel
website address www.orchardtable.com
email address brim@orchardtable.com

Should be easy quick job, prompt + detailed feedback given, am online in UK 9am-10pm for next 3 days. Website is www.orchardtable.com

Industry/Entity Type

Business

Requirements
Must have
• The logo must be corrected. The kerning is not right.

Please use a warm-grey for text

Please submit in matt format, we will be printing matt finish.

Should not have
• Avoid using banners or curvy highlights

Please avoid using black

Please avoid submitting in gloss finish

```html
<!DOCTYPE html>
<html lang="en">
<head>
<meta charset="utf-8">
<title>Brim — Business Card</title>
<link rel="stylesheet" href="https://fonts.googleapis.com/css2?family=Cinzel:wght@400;600;700&display=swap">
<style>
  :root {
    --backdrop: #e8e8e7;
    --card-yellow: #f3e670;
    --card-white: #fbfbfa;
    --warm-grey: #57534f;
    --logo-yellow: #efe46b;
  }
  * { box-sizing: border-box; margin: 0; padding: 0; }
  html, body {
    width: 1200px;
    height: 720px;
    overflow: hidden;
    background: var(--backdrop);
  }
  .canvas {
    position: relative;
    width: 1200px;
    height: 720px;
    font-family: "Cinzel", Georgia, serif;
  }
  .card {
    position: absolute;
    top: 242px;
    width: 420px;
    height: 238px;
  }
  .card--front {
    left: 147px;
    background: var(--card-yellow);
    color: var(--warm-grey);
  }
  .card--back {
    left: 633px;
    background: var(--card-white);
    border: 1px solid #dcdcda;
  }
  .card__wordmark {
    position: absolute;
    left: 22px;
    top: 22px;
    font-size: 52px;
    font-weight: 600;
    line-height: 1;
    letter-spacing: 2px;
    color: var(--warm-grey);
  }
  .contact-list {
    position: absolute;
    left: 22px;
    top: 169px;
    list-style: none;
    font-size: 9.5px;
    line-height: 12px;
    color: var(--warm-grey);
  }
  .contact-list li {
    display: flex;
    align-items: center;
    gap: 8px;
  }
  .contact-list svg {
    width: 10px;
    height: 9px;
    flex: none;
    fill: var(--warm-grey);
  }
  .card__name {
    position: absolute;
    right: 15px;
    bottom: 27px;
    font-size: 12px;
    font-weight: 700;
    font-variant: small-caps;
    letter-spacing: 0.3px;
  }
  .card__logo-block {
    position: absolute;
    left: 0;
    right: 0;
    top: 72px;
    text-align: center;
    color: var(--logo-yellow);
  }
  .card__logo-block .logo {
    font-size: 70px;
    font-weight: 600;
    line-height: 1;
    letter-spacing: 3px;
  }
  .card__logo-block .tagline {
    margin-top: 10px;
    font-size: 11px;
    font-weight: 400;
    letter-spacing: 0.3px;
  }
</style>
</head>
<body>
<main class="canvas">
  <section class="card card--front" aria-label="Card front">
    <div class="card__wordmark">BRIM</div>
    <ul class="contact-list">
      <li>
        <svg viewBox="0 0 10 9" aria-hidden="true"><path d="M1 2.5C1 1.5 3 1 5 1s4 .5 4 1.5V4H7V3H3v1H1zM2 5h6l1 3H1z"/></svg>
        +44 7700900463
      </li>
      <li>
        <svg viewBox="0 0 10 9" aria-hidden="true"><path d="M0 1h10v7H0zM1 2v.3l4 3 4-3V2zm0 1.5V7h8V3.5L5 6.5z" fill-rule="evenodd"/></svg>
        BRIM@ORCHARDTABLE.COM
      </li>
      <li>
        <svg viewBox="0 0 10 9" aria-hidden="true"><rect x="0.5" y="0" width="9" height="9"/></svg>
        @BRIMCOUNSEL
      </li>
      <li>
        <svg viewBox="0 0 10 9" aria-hidden="true"><path d="M0 0h10v6.5H0zM1 1v4.5h8V1zM3.5 7h3l.5 2H3z" fill-rule="evenodd"/></svg>
        WWW.ORCHARDTABLE.COM
      </li>
    </ul>
    <div class="card__name">Rosalind Whitcombe</div>
  </section>

  <section class="card card--back" aria-label="Card back">
    <div class="card__logo-block">
      <div class="logo">BRIM</div>
      <div class="tagline">PLANT-BASED FOOD CONSULTING</div>
    </div>
  </section>
</main>
</body>
</html>
```